32 x 24 Swinging Real Estate Yard Sign

We are looking to design a new sign for our business to focus on the remodeling of homes to sell. We are looking to have a yard sign that gets peoples attention and is informational. The headline will be "The Secret to Top Dollar? Remodel First.". We remodel homes for sellers with no up front cost, as they simply pay at closing. This link has more info, https://bramblecresthomes.com/Remodel
The message we want to convey to those seeing the sign is we are a one stop shop, who can renovate your home and sell it for no stress. We are licensed real estate agents and licensed contractors.
Both of these license numbers and info need to be on the design:
CADRE #02794613
Contractors License #1178524
Email: info@bramblecresthomes.com
Phone: (408)614-2907
I'll attach a sample sign we have for our agents normally as well as all brand art work.
• Pantone Colors
o #172A41
Dark blue
o #4381B1
Medium blue
o #6FA6CC
Light blue
Target Market(s)
Residential Real Estate Sellers
Industry/Entity Type
Real Estate
Colors
Designer to choose colors to be used in the design.

```html
<!DOCTYPE html>
<html lang="en">
<head>
<meta charset="utf-8">
<title>Bramblecrest Homes – Remodel First Yard Sign</title>
<link rel="stylesheet" href="https://fonts.googleapis.com/css2?family=Jost:wght@500;600;700&family=Poppins:wght@500;600&family=Roboto:wght@700&display=swap">
<style>
  :root {
    --backdrop: #808080;
    --navy: #172a41;
    --navy-soft: #213551;
    --band-blue: #3b6a91;
    --headline-blue: #2e76b0;
    --badge-blue: #3d6a90;
    --white: #ffffff;
  }
  * { margin: 0; padding: 0; box-sizing: border-box; }
  html, body {
    width: 981px; height: 1200px; overflow: hidden;
    background: var(--backdrop);
  }
  .yard-sign {
    position: absolute; left: 120px; top: 106px;
    width: 742px; height: 988px;
    background: var(--navy);
    overflow: hidden;
  }
  .sign-curves { position: absolute; inset: 0; width: 742px; height: 988px; }
  .centered {
    position: absolute; left: 0; right: 0;
    text-align: center; white-space: nowrap;
  }
  .brand-name {
    top: 78px;
    font-family: 'Jost', sans-serif; font-weight: 600;
    font-size: 44px; line-height: 50px; letter-spacing: 1px;
    color: var(--navy);
  }
  .headline-lead {
    top: 190px;
    font-family: 'Jost', sans-serif; font-weight: 600;
    font-size: 54px; line-height: 60px;
    color: var(--headline-blue);
  }
  .headline-question {
    top: 244px;
    font-family: 'Jost', sans-serif; font-weight: 700;
    font-size: 70px; line-height: 76px;
    color: var(--headline-blue);
  }
  .headline-answer {
    top: 318px;
    font-family: 'Jost', sans-serif; font-weight: 700;
    font-size: 128px; line-height: 116px;
    color: var(--navy);
  }
  .license-row {
    position: absolute; top: 713px; left: 49px; right: 48px;
    display: flex; justify-content: space-between;
  }
  .license-badge {
    display: flex; height: 35px; border-radius: 12px;
    background: var(--badge-blue); overflow: hidden;
    font-family: 'Poppins', sans-serif; font-size: 20px; line-height: 35px;
  }
  .license-badge .label {
    background: var(--white); color: var(--navy); font-weight: 500;
    border-radius: 12px; padding: 0 14px;
  }
  .license-badge .number { color: var(--white); font-weight: 600; padding: 0 10px 0 12px; }
  .badge-cadre { width: 250px; }
  .badge-cadre .label { width: 107px; }
  .badge-contractor { width: 381px; }
  .badge-contractor .label { width: 252px; }
  .contact-email {
    top: 778px;
    font-family: 'Roboto', sans-serif; font-weight: 700;
    font-size: 49px; line-height: 60px;
    color: var(--white);
  }
  .contact-phone {
    top: 838px;
    font-family: 'Jost', sans-serif; font-weight: 600;
    font-size: 104px; line-height: 118px; letter-spacing: -1px;
    color: var(--white);
  }
</style>
</head>
<body>
  <main class="yard-sign">
    <svg class="sign-curves" viewBox="0 0 742 988" aria-hidden="true">
      <path class="swoosh-left" fill="var(--navy-soft)" d="M0,390 C70,560 200,640 215,652 C120,636 40,600 0,570 Z"/>
      <path class="swoosh-right" fill="var(--navy-soft)" d="M742,487 C700,600 640,660 540,688 C620,690 700,660 742,640 Z"/>
      <path class="arc-band" fill="var(--band-blue)" d="M0,385 C80,540 250,677 413,677 C560,677 680,590 742,487 V385 Z"/>
      <path class="arc-white" fill="var(--white)" d="M0,0 H742 V385 C650,560 520,612 371,611 C220,610 70,520 0,385 Z"/>
    </svg>

    <div class="centered brand-name">BRAMBLECREST HOMES</div>

    <h1 class="headline">
      <span class="centered headline-lead">THE SECRET TO</span>
      <span class="centered headline-question">TOP DOLLAR?</span>
      <span class="centered headline-answer">REMODEL<br>FIRST</span>
    </h1>

    <div class="license-row">
      <div class="license-badge badge-cadre">
        <span class="label">CADRE</span><span class="number">#02794613</span>
      </div>
      <div class="license-badge badge-contractor">
        <span class="label">Contractors License</span><span class="number">#1178524</span>
      </div>
    </div>

    <div class="centered contact-email">info@bramblecresthomes.com</div>
    <div class="centered contact-phone">(408)614-2907</div>
  </main>
</body>
</html>
```